New, modern business card for growing audiology practice

We need a new business card for our audiology practice. Our logo and website have recently changed (more modern) and we want our business cards to reflect this change.
We conduct hearing tests, perform earwax removals, and fit & dispense hearing aids to our patients. We are a family owned practice in which the owner is the one who works directly with the patient. I have attached logos in various formats to use, as well as two ideas I found on this website; as well as a scanned copy of our current logo. Good luck!

Industry/Entity Type

Business

Contact Information for Business Card

Company name: Tolvera Hearing Center
Provider name: Peter Wolstenby, Au.D. F/NSB
Phone number: (440) 683-5127
Address: 837 W. Lindell Ave. Marlow Falls, OH 44871
email: tolverahearing@postvane.com
website: tolverahearing.com

Colors
000000
aaaaaa
dbdbdb
cacaca
9bcb3c
afd23c
cadf82
b1b1b1

Requirements
Must have
• My card must include information in the "details" section. In the attached images, I found a few that I liked and I would like to model after - "brisky bouncin'" and "Sound Method Center".
• Must be horizontal.
• Must include logos provided. I uploaded them in various file formats and various ways.
• Must match logo font, if possible, if not, please get as close as you can.
Nice to have
• I really like the idea of having a color on one side with just the logo and company name and the contact information and provider name on the other side. I also really like the idea of having the main color dominating on the logo/company side with accent of that same color on the contact side of the card.
Should not have
• Must not be vertical.

```html
<!DOCTYPE html>
<html lang="en">
<head>
<meta charset="utf-8">
<title>Tolvera Hearing Center – Business Card</title>
<link rel="stylesheet" href="https://fonts.googleapis.com/css2?family=Roboto:wght@400;500;700&family=Roboto+Condensed:wght@700&display=swap">
<style>
  :root {
    --backdrop: #6f5540;
    --card-light: #f4f4f3;
    --card-dark: #1b1c1e;
    --brand-green: #79aa3a;
    --ink: #111111;
    --ink-soft: #555555;
    --white: #ffffff;
  }
  * { margin: 0; padding: 0; box-sizing: border-box; }
  html, body { width: 1200px; height: 960px; overflow: hidden; }
  body {
    position: relative;
    background: var(--backdrop);
    font-family: "Roboto", Arial, sans-serif;
  }
  .card {
    position: absolute;
    width: 600px;
    height: 342px;
    border-radius: 20px;
    box-shadow: 2px 4px 8px rgba(0,0,0,0.35);
    overflow: hidden;
  }
  .card-front { left: 314px; top: 113px; background: var(--card-light); }
  .card-back  { left: 311px; top: 472px; background: var(--card-dark); }

  .front-brand {
    position: absolute;
    left: 0; right: 0; top: 56px;
    display: flex; align-items: center; justify-content: center; gap: 14px;
  }
  .brand-dot {
    width: 30px; height: 30px; border-radius: 50%;
    background: var(--brand-green);
  }
  .brand-name {
    font-family: "Roboto", Arial, sans-serif;
    font-weight: 500;
    font-size: 32px;
    letter-spacing: 0.5px;
    color: var(--ink);
    text-transform: uppercase;
  }

  .accent-bar {
    position: absolute; left: 0; top: 170px;
    width: 15px; height: 42px;
    background: var(--brand-green);
  }
  .provider { position: absolute; left: 38px; top: 169px; }
  .provider-name {
    font-family: "Roboto Condensed", "Arial Narrow", sans-serif;
    font-weight: 700; font-size: 21px;
    color: var(--brand-green);
    line-height: 26px;
  }
  .provider-credentials {
    font-weight: 700; font-size: 15px;
    color: var(--ink);
    line-height: 20px;
  }

  .contact-list {
    position: absolute; left: 38px; top: 252px;
    list-style: none;
  }
  .contact-item {
    display: flex; align-items: center; gap: 8px;
    font-size: 14.5px; color: var(--ink-soft);
    line-height: 19px;
  }
  .contact-icon { width: 14px; height: 14px; flex: none; }

  .address {
    position: absolute; right: 37px; top: 271px;
    text-align: right;
    font-size: 14.5px; line-height: 19px;
    color: var(--ink-soft);
    font-style: normal;
  }

  .back-brand {
    position: absolute; left: 0; right: 0; top: 88px;
    display: flex; flex-direction: column; align-items: center; gap: 22px;
  }
  .back-dot {
    width: 84px; height: 84px; border-radius: 50%;
    background: var(--brand-green);
  }
  .back-name {
    font-weight: 500; font-size: 28px; letter-spacing: 1px;
    color: var(--brand-green);
    text-transform: uppercase;
  }
  .back-web {
    position: absolute; left: 0; right: 0; top: 294px;
    text-align: center;
    font-size: 14px; letter-spacing: 4px;
    color: var(--white);
  }
</style>
</head>
<body>

<section class="card card-front">
  <div class="front-brand">
    <span class="brand-dot"></span>
    <span class="brand-name">Tolvera Hearing Center</span>
  </div>

  <span class="accent-bar"></span>
  <div class="provider">
    <p class="provider-name">PETER WOLSTENBY</p>
    <p class="provider-credentials">AU.D. F/NSB</p>
  </div>

  <ul class="contact-list">
    <li class="contact-item">
      <svg class="contact-icon" viewBox="0 0 16 16" aria-hidden="true"><path fill="#79aa3a" d="M3.6 1.2l2.3 2.6c.3.4.3.9 0 1.2L4.8 6.2c.8 1.9 2.5 3.6 4.4 4.5l1.2-1.1c.4-.3.9-.3 1.2 0l2.6 2.3c.4.3.4.9 0 1.3l-1.3 1.3c-.7.7-1.8.8-2.7.4C6.2 13.4 2.6 9.8 1.1 5.8.7 4.9.9 3.8 1.6 3.1L2.3 2.4c.4-.4.9-.5 1.3-1.2z"/></svg>
      (440) 683-5127
    </li>
    <li class="contact-item">
      <svg class="contact-icon" viewBox="0 0 16 16" aria-hidden="true"><rect x="1" y="3" width="14" height="10" rx="1" fill="#79aa3a"/><path d="M1.5 4l6.5 5 6.5-5" fill="none" stroke="#f4f4f3" stroke-width="1.3"/></svg>
      tolverahearing@postvane.com
    </li>
    <li class="contact-item">
      <svg class="contact-icon" viewBox="0 0 16 16" aria-hidden="true"><circle cx="8" cy="8" r="7" fill="#79aa3a"/><path d="M1 8h14M8 1c2.5 2.5 2.5 11.5 0 14M8 1c-2.5 2.5-2.5 11.5 0 14" fill="none" stroke="#f4f4f3" stroke-width="1"/></svg>
      tolverahearing.com
    </li>
  </ul>

  <address class="address">837 W. Lindell Ave.<br>Marlow Falls, OH 44871</address>
</section>

<section class="card card-back">
  <div class="back-brand">
    <span class="back-dot"></span>
    <span class="back-name">Tolvera Hearing Center</span>
  </div>
  <p class="back-web">www.tolverahearing.com</p>
</section>

</body>
</html>
```